update of B2B website and conversion to single page

The current website needs to be modernized. I want what is commonly called a single page website. It is not actually a single page. See some examples here:
https://www.plivenor.example/
https://www.quorbel.example/
https://www.trindavex.example/
Most or all graphics will be replaced.
Please see the attached spreadsheet for a rough draft of the home page layout. Convert the existing website at https://www.zolvarin.example/ to a single page website. We will provide the page content. You will provide all of the design, graphics, development, production deployment. etc. The look and feel should be corporate, polished, premium.

```html
<!DOCTYPE html>
<html lang="en">
<head>
<meta charset="utf-8">
<title>Zolvarin — Enterprise Data Quality</title>
<link href="https://fonts.googleapis.com/css2?family=Oswald:wght@400;500;600&family=Poppins:wght@300;400;500&display=swap" rel="stylesheet">
<style>
:root{
  --navy:#2c2f6d;
  --navy-deep:#23265a;
  --gold:#fbb615;
  --ink:#1b1b1b;
  --muted:#555;
  --white:#fff;
  --footer:#050505;
  --footer-text:#9a9a9a;
}
*{margin:0;padding:0;box-sizing:border-box}
html,body{width:1200px;height:3125px;overflow:hidden}
body{position:relative;background:var(--white);font-family:'Poppins',sans-serif;color:var(--ink)}
.abs{position:absolute}
svg{display:block}

/* header */
.topbar{left:385px;top:0;width:815px;height:52px;background:var(--navy);clip-path:polygon(0 0,100% 0,100% 100%,30px 100%)}
.topbar-item{top:16px;color:var(--white);font-size:15px;display:flex;align-items:center;gap:14px;white-space:nowrap}
.social-dot{width:14px;height:14px;border-radius:50%;background:var(--white)}
.brand{left:112px;top:24px;display:flex;align-items:center;gap:10px}
.brand-mark{width:30px;height:30px;border-radius:50%;background:var(--gold)}
.brand-name{font-size:32px;font-weight:500;color:var(--navy);line-height:1}
.brand-tag{left:210px;top:70px;font-size:11px;font-weight:500;color:var(--navy);white-space:nowrap}
.nav{top:72px;font-size:14.5px;color:#333;white-space:nowrap}

/* hero */
.hero{left:0;top:108px;width:1200px;height:419px;background:linear-gradient(135deg,#5a6592 0%,#4a5586 45%,#3b4577 100%)}
.hero-title{left:0;top:220px;width:1200px;text-align:center;font-family:'Oswald',sans-serif;font-weight:500;font-size:82px;color:var(--white);line-height:1}
.hero-sub{left:0;top:328px;width:1200px;text-align:center;font-size:23px;color:var(--white);line-height:34px}

/* highlights */
.strip{top:527px;width:300px;height:148px;display:flex;align-items:center;padding-left:58px;gap:24px}
.strip.navy{background:var(--navy)}
.strip.gold{background:var(--gold)}
.strip-easy{font-size:54px;font-weight:300;color:var(--white)}
.strip-text{font-size:16px;line-height:27px;color:var(--white);white-space:nowrap}
.strip.gold .strip-text{color:#fff6dd}

/* section headings */
.section-title{left:0;width:1200px;text-align:center;font-family:'Oswald',sans-serif;font-weight:600;font-size:46px;color:var(--ink);line-height:1}
.section-title span{color:var(--gold)}

/* services */
.photo{background:linear-gradient(135deg,#c9cfd6,#7d8894 60%,#4f5864)}
.photo.office{background:linear-gradient(135deg,#d8d4cc,#a9a49a 45%,#3c4046)}
.svc-icon{width:80px;height:80px;border-radius:50%;background:var(--navy);display:flex;align-items:center;justify-content:center}
.svc-title{font-size:27px;font-weight:400;color:var(--ink);line-height:42px}
.svc-list{list-style:none;font-size:14.5px;color:#222}
.svc-list li{height:34px}

/* connectors */
.group-title{left:112px;font-size:23px;font-weight:500;color:var(--ink)}
.conn{display:flex;align-items:center;gap:20px;font-size:16px;color:#222;white-space:nowrap}
.conn-icon{width:48px;height:48px;border-radius:50%;background:var(--gold);display:flex;align-items:center;justify-content:center}

/* support */
.card{top:2435px;width:312px;height:255px}
.card-photo{position:absolute;left:0;top:0;width:100%;display:flex;align-items:center;justify-content:center;font-family:'Oswald',sans-serif;font-size:26px;letter-spacing:2px;color:var(--white);white-space:nowrap}
.card-label{position:absolute;left:0;bottom:0;width:100%;display:flex;align-items:center;justify-content:center;text-align:center;font-size:18px;font-weight:500;color:var(--white);background:var(--navy)}
.card-label.gold{background:var(--gold);color:var(--ink)}

/* footer */
.footer{left:0;top:2760px;width:1200px;height:365px;background:var(--footer)}
.f-head{font-size:17px;color:#bdbdbd}
.f-small{font-family:'Oswald',sans-serif;font-weight:400;font-size:13px;color:var(--footer-text)}
.f-links{list-style:none;font-family:'Oswald',sans-serif;font-size:13px;color:var(--footer-text)}
.f-links li{height:26px}
.newsletter{left:100px;top:2900px;width:265px;height:35px;background:var(--white);border-radius:18px;display:flex;align-items:center;justify-content:space-between;padding:3px}
.newsletter-field{padding-left:16px;font-size:12px;color:#999}
.newsletter-btn{height:29px;padding:0 20px;border-radius:15px;background:var(--gold);font-size:12px;font-weight:500;color:var(--ink);display:flex;align-items:center}
.f-social{left:100px;top:2984px;display:flex;gap:22px}
.f-social span{width:13px;height:13px;border-radius:50%;background:var(--white)}
</style>
</head>
<body>

<!-- header -->
<div class="abs topbar"></div>
<div class="abs topbar-item" style="left:478px">
  <svg width="16" height="16" viewBox="0 0 24 24"><path fill="#fff" d="M6.6 10.8a15 15 0 0 0 6.6 6.6l2.2-2.2c.3-.3.7-.4 1-.2 1.1.4 2.3.6 3.6.6.6 0 1 .4 1 1V20c0 .6-.4 1-1 1A17 17 0 0 1 3 4c0-.6.4-1 1-1h3.5c.6 0 1 .4 1 1 0 1.3.2 2.5.6 3.6.1.3 0 .7-.2 1z"/></svg>
  <span>(555) 014-2287</span>
</div>
<div class="abs topbar-item" style="left:690px">
  <svg width="18" height="14" viewBox="0 0 24 18"><path fill="#fff" d="M0 0h24v18H0z"/><path fill="none" stroke="#2c2f6d" stroke-width="2" d="M1 1l11 9 11-9"/></svg>
  <span>info@zolvarin.example</span>
</div>
<div class="abs topbar-item" style="left:925px;top:19px;gap:22px" aria-label="Social links">
  <span class="social-dot"></span><span class="social-dot"></span><span class="social-dot"></span><span class="social-dot"></span><span class="social-dot"></span>
</div>

<div class="abs brand"><span class="brand-mark"></span><span class="brand-name">Zolvarin</span></div>
<div class="abs brand-tag">Enterprise Data Quality Made Easy</div>

<div class="abs nav" style="left:462px">Home</div>
<div class="abs nav" style="left:542px">Features</div>
<div class="abs nav" style="left:641px">Services</div>
<div class="abs nav" style="left:737px">Rich Connectors</div>
<div class="abs nav" style="left:886px">Support</div>
<div class="abs nav" style="left:980px">Contact</div>
<svg class="abs" style="left:1070px;top:74px" width="15" height="15" viewBox="0 0 24 24"><circle cx="10" cy="10" r="7" fill="none" stroke="#222" stroke-width="3"/><path d="M15 15l7 7" stroke="#222" stroke-width="3"/></svg>

<!-- hero -->
<div class="abs hero" role="img" aria-label="Hands typing on a laptop overlaid with glowing data icons, tinted blue"></div>
<svg class="abs" style="left:40px;top:296px" width="30" height="46" viewBox="0 0 30 46"><path d="M24 4L6 23l18 19" fill="none" stroke="#fff" stroke-width="5"/></svg>
<svg class="abs" style="left:1132px;top:296px" width="30" height="46" viewBox="0 0 30 46"><path d="M6 4l18 19L6 42" fill="none" stroke="#fff" stroke-width="5"/></svg>
<h1 class="abs hero-title">Zolvarin</h1>
<p class="abs hero-sub">Enterprise Data Quality and Master Data<br>Management Made Easy</p>

<!-- highlights -->
<div class="abs strip navy" style="left:0;padding-left:90px"><span class="strip-easy">Easy</span></div>
<div class="abs strip gold" style="left:300px">
  <svg width="26" height="36" viewBox="0 0 24 34"><path fill="#fff" d="M12 0C5.4 0 0 5.4 0 12c0 9 12 22 12 22s12-13 12-22C24 5.4 18.6 0 12 0zm0 17a5 5 0 1 1 0-10 5 5 0 0 1 0 10z"/></svg>
  <span class="strip-text">Cleanse addresses<br>in 5 minutes</span>
</div>
<div class="abs strip navy" style="left:600px;padding-left:44px;gap:20px">
  <svg width="40" height="32" viewBox="0 0 40 32"><path d="M0 7h10c8 0 12 18 20 18h6M0 25h10c3 0 5-2 7-6M23 12c2-3 4-5 7-5h6" fill="none" stroke="#fff" stroke-width="4"/><path fill="#fff" d="M34 0l6 7-6 7zM34 18l6 7-6 7z"/></svg>
  <span class="strip-text">Match and Merge<br>records in 10 minutes</span>
</div>
<div class="abs strip gold" style="left:900px">
  <svg width="34" height="34" viewBox="0 0 34 34"><circle cx="17" cy="17" r="14" fill="none" stroke="#fff" stroke-width="4"/><path d="M17 9v9h7" fill="none" stroke="#fff" stroke-width="4"/></svg>
  <span class="strip-text">Master records in<br>60 minutes</span>
</div>

<!-- services -->
<h2 class="abs section-title" style="top:764px">Our <span>Services</span></h2>

<div class="abs photo" style="left:112px;top:850px;width:488px;height:373px" role="img" aria-label="Developer working at a desk with several monitors"></div>
<div class="abs svc-icon" style="left:693px;top:960px">
  <svg width="40" height="40" viewBox="0 0 40 40"><ellipse cx="18" cy="8" rx="13" ry="5" fill="none" stroke="#fff" stroke-width="2.5"/><path d="M5 8v20c0 3 6 5 13 5M31 8v8M5 18c0 3 6 5 13 5" fill="none" stroke="#fff" stroke-width="2.5"/><circle cx="29" cy="28" r="8" fill="none" stroke="#fff" stroke-width="2.5"/><path d="M25 28l3 3 5-6" fill="none" stroke="#fff" stroke-width="2.5"/></svg>
</div>
<div class="abs svc-title" style="left:815px;top:952px">Data Quality</div>
<ul class="abs svc-list" style="left:815px;top:1018px">
  <li>Global Address Verification</li>
  <li>Data Cleansing/Enrichment</li>
  <li>Match and Merge</li>
</ul>

<div class="abs photo office" style="left:600px;top:1223px;width:485px;height:373px" role="img" aria-label="Two colleagues reviewing a laptop showing a bar chart"></div>
<div class="abs svc-icon" style="left:146px;top:1316px">
  <svg width="42" height="42" viewBox="0 0 42 42"><circle cx="21" cy="21" r="4" fill="#fff"/><circle cx="21" cy="6" r="3" fill="#fff"/><circle cx="6" cy="30" r="3" fill="#fff"/><circle cx="36" cy="30" r="3" fill="#fff"/><circle cx="13" cy="36" r="3" fill="#fff"/><circle cx="29" cy="36" r="3" fill="#fff"/><path d="M21 21V6M21 21L6 30M21 21l15 9M21 21l-8 15M21 21l8 15" stroke="#fff" stroke-width="2"/></svg>
</div>
<div class="abs svc-title" style="left:267px;top:1306px">Master Data<br>Management</div>
<ul class="abs svc-list" style="left:267px;top:1408px">
  <li>Integration</li>
  <li>Mastering</li>
  <li>Governance</li>
</ul>

<!-- connectors -->
<h2 class="abs section-title" style="top:1681px">Rich <span>Connectors</span></h2>

<div class="abs group-title" style="top:1767px">Applications</div>
<div class="abs conn" style="left:112px;top:1820px"><span class="conn-icon"><svg width="24" height="24" viewBox="0 0 24 24"><rect x="2" y="2" width="8" height="8" fill="#fff"/><rect x="14" y="2" width="8" height="8" fill="#fff"/><rect x="2" y="14" width="8" height="8" fill="#fff"/><rect x="14" y="14" width="8" height="8" fill="#fff"/></svg></span>Trindavex</div>
<div class="abs conn" style="left:471px;top:1820px"><span class="conn-icon"><svg width="24" height="24" viewBox="0 0 24 24"><circle cx="8" cy="8" r="5" fill="none" stroke="#fff" stroke-width="2.5"/><circle cx="16" cy="16" r="5" fill="none" stroke="#fff" stroke-width="2.5"/></svg></span>FieldMaven</div>
<div class="abs conn" style="left:831px;top:1820px"><span class="conn-icon"><svg width="24" height="24" viewBox="0 0 24 24"><circle cx="12" cy="12" r="9" fill="none" stroke="#fff" stroke-width="2.5"/><path d="M12 6v6h5" fill="none" stroke="#fff" stroke-width="2.5"/></svg></span>Corvane CRM</div>
<div class="abs conn" style="left:112px;top:1895px"><span class="conn-icon"><svg width="24" height="24" viewBox="0 0 24 24"><rect x="3" y="4" width="18" height="16" rx="2" fill="none" stroke="#fff" stroke-width="2.5"/><path d="M3 9h18M9 9v11" stroke="#fff" stroke-width="2"/></svg></span>Orvello E-Business Suite</div>
<div class="abs conn" style="left:471px;top:1895px"><span class="conn-icon"><svg width="24" height="24" viewBox="0 0 24 24"><rect x="3" y="3" width="8" height="8" fill="#fff"/><rect x="13" y="3" width="8" height="8" fill="#fff"/><rect x="3" y="13" width="8" height="8" fill="#fff"/><rect x="13" y="13" width="8" height="8" fill="#fff"/></svg></span>Mircast Dynamo*</div>
<div class="abs conn" style="left:831px;top:1895px"><span class="conn-icon"><svg width="24" height="24" viewBox="0 0 24 24"><rect x="3" y="6" width="18" height="12" rx="2" fill="#fff"/></svg></span>Brevik ERP*</div>

<div class="abs group-title" style="top:1965px">Databases</div>
<div class="abs conn" style="left:112px;top:2018px"><span class="conn-icon"><svg width="22" height="24" viewBox="0 0 22 24"><ellipse cx="11" cy="5" rx="8" ry="3" fill="#fff"/><path d="M3 5v14c0 2 4 3 8 3s8-1 8-3V5" fill="none" stroke="#fff" stroke-width="2.5"/><path d="M3 12c0 2 4 3 8 3s8-1 8-3" fill="none" stroke="#fff" stroke-width="2"/></svg></span>Orvello DB</div>
<div class="abs conn" style="left:471px;top:2018px"><span class="conn-icon"><svg width="22" height="24" viewBox="0 0 22 24"><path d="M4 2h10l5 5v15H4z" fill="none" stroke="#fff" stroke-width="2.5"/><path d="M7 16h9" stroke="#fff" stroke-width="2"/></svg></span>LumaBase</div>
<div class="abs conn" style="left:831px;top:2018px"><span class="conn-icon"><svg width="22" height="24" viewBox="0 0 22 24"><ellipse cx="11" cy="5" rx="8" ry="3" fill="#fff"/><path d="M3 5v14c0 2 4 3 8 3s8-1 8-3V5" fill="none" stroke="#fff" stroke-width="2.5"/></svg></span>Mircast Datastore</div>
<div class="abs conn" style="left:112px;top:2093px"><span class="conn-icon"><svg width="22" height="24" viewBox="0 0 22 24"><ellipse cx="11" cy="5" rx="8" ry="3" fill="#fff"/><path d="M3 5v14c0 2 4 3 8 3s8-1 8-3V5" fill="none" stroke="#fff" stroke-width="2.5"/><path d="M3 12c0 2 4 3 8 3s8-1 8-3" fill="none" stroke="#fff" stroke-width="2"/></svg></span>PelicanBase</div>
<div class="abs conn" style="left:471px;top:2093px"><span class="conn-icon"><svg width="22" height="24" viewBox="0 0 22 24"><rect x="3" y="2" width="16" height="20" rx="2" fill="none" stroke="#fff" stroke-width="2.5"/><path d="M7 8h8M7 13h8" stroke="#fff" stroke-width="2"/></svg></span>Ivorn Ledger</div>
<div class="abs conn" style="left:831px;top:2093px"><span class="conn-icon"><svg width="24" height="24" viewBox="0 0 24 24"><circle cx="10" cy="10" r="7" fill="none" stroke="#fff" stroke-width="2.5"/><circle cx="17" cy="17" r="5" fill="#fff"/></svg></span>Veradune*</div>

<div class="abs group-title" style="top:2163px">Files</div>
<div class="abs conn" style="left:112px;top:2218px"><span class="conn-icon"><svg width="22" height="24" viewBox="0 0 22 24"><path d="M4 2h10l5 5v15H4z" fill="none" stroke="#fff" stroke-width="2.5"/><path d="M7 11h9M7 15h9M7 19h9" stroke="#fff" stroke-width="1.8"/></svg></span>CSV</div>
<div class="abs conn" style="left:471px;top:2218px"><span class="conn-icon"><svg width="22" height="24" viewBox="0 0 22 24"><path d="M4 2h10l5 5v15H4z" fill="none" stroke="#fff" stroke-width="2.5"/><path d="M7 12h9M7 17h6" stroke="#fff" stroke-width="1.8"/></svg></span>Delimited</div>
<div class="abs conn" style="left:831px;top:2218px"><span class="conn-icon"><svg width="22" height="24" viewBox="0 0 22 24"><path d="M4 2h10l5 5v15H4z" fill="none" stroke="#fff" stroke-width="2.5"/><path d="M8 11l6 7M14 11l-6 7" stroke="#fff" stroke-width="2"/></svg></span>Gridsheet</div>

<!-- support -->
<h2 class="abs section-title" style="top:2354px">Support</h2>

<div class="abs card" style="left:112px">
  <div class="card-photo" style="height:194px;background:linear-gradient(135deg,#c6c2ba,#8c8a86 55%,#5d6068)" role="img" aria-label="Hand holding a phone over a notebook">BATCH</div>
  <div class="card-label" style="height:61px">On your schedule</div>
</div>
<div class="abs card" style="left:444px">
  <div class="card-photo" style="height:194px;background:linear-gradient(135deg,#a9b0b8,#6f7782 55%,#4a5159)" role="img" aria-label="Laptop keyboard with floating network icons">STREAMING</div>
  <div class="card-label gold" style="height:61px">Always in sync</div>
</div>
<div class="abs card" style="left:775px;width:310px">
  <div class="card-photo" style="height:169px;background:linear-gradient(135deg,#3a2c24,#8a5a34 50%,#d08a3c)" role="img" aria-label="Person using an interactive screen in a warmly lit room">REAL TIME/INTERACTIVE</div>
  <div class="card-label" style="height:86px;line-height:28px">Autocomplete Anything<br>Smart Search</div>
</div>

<!-- footer -->
<footer class="abs footer"></footer>
<div class="abs f-head" style="left:100px;top:2815px">Newsletter</div>
<div class="abs f-small" style="left:100px;top:2857px">Get More Informations</div>
<div class="abs newsletter"><span class="newsletter-field">Email Address</span><span class="newsletter-btn">SUBSCRIBE</span></div>
<div class="abs f-social" aria-label="Social links"><span></span><span></span><span></span><span></span><span></span></div>

<div class="abs f-head" style="left:720px;top:2815px">Importants</div>
<ul class="abs f-links" style="left:720px;top:2857px">
  <li>Home</li><li>Features</li><li>Services</li><li>Rich Connectors</li><li>Support</li><li>Contact us</li>
</ul>
<div class="abs f-head" style="left:908px;top:2815px">Other</div>
<ul class="abs f-links" style="left:908px;top:2857px">
  <li>Privacy Policy</li><li>Faq</li><li>Terms &amp; Conditions</li>
</ul>
<div class="abs f-small" style="left:800px;top:3074px;width:300px;text-align:right">© 2018 Copyrights Zolvarin All Rights Reserved</div>

</body>
</html>
```